Meridale Nutrition needs Stationary and a business card

We would like to use our current logo. The text can be moved around as needed. The stationary needs to be a 'first page' where the logo is more prominent to be impressive on higher quality paper and a second page where the logo is more subtle where there will be much more information on the page. There are 2 clinic locations which will need include name, address, phone number, fax number, web address. The business card should be single sided and contain this information also.
The design must be contemporary and sophisticated as this is a science based diet run out of a medical clinic.

Target Market(s)

People wanting to lose weight, athletes looking to optimise performance, people with arthritis or fighting cancer

Industry/Entity Type

Business

Contact Information for Business Card

must use the logo. I have attached an example card with the practice details on it. there must be space for the doctors name. Also the website www.meridalenutrition.com.au

Requirements
Must have
• the logo, the business adresses and phone numbers, the website, the doctors name and qualifications
Nice to have
• some creativity
Should not have
• Do not simply reproduce the existing card please

```html
<!DOCTYPE html>
<html lang="en">
<head>
<meta charset="utf-8">
<title>Meridale Nutrition – Business Card</title>
<link rel="stylesheet" href="https://fonts.googleapis.com/css2?family=PT+Sans:wght@400;700&family=PT+Sans+Narrow:wght@400&display=swap">
<style>
  :root {
    --backdrop: #3b3b3b;
    --card: #f7f7f7;
    --navy: #2b5b93;
    --cyan: #1ab0ea;
    --ink: #555555;
  }
  html, body {
    margin: 0;
    width: 1200px;
    height: 750px;
    overflow: hidden;
    background: var(--backdrop);
  }
  .card {
    position: absolute;
    left: 100px;
    top: 89px;
    width: 1000px;
    height: 571px;
    background: var(--card);
    font-family: "PT Sans", sans-serif;
    color: var(--ink);
  }
  .card > * { position: absolute; margin: 0; line-height: 1; white-space: nowrap; }

  .brand-mark { left: 724px; top: 40px; width: 170px; height: 170px; }
  .brand-name {
    left: 609px; width: 400px; top: 216px;
    text-align: center;
    font-size: 30px; font-weight: 700; color: var(--navy);
  }
  .brand-web {
    left: 609px; width: 400px; top: 256px;
    text-align: center;
    font-size: 20px; color: var(--ink);
  }

  .doctor-name { left: 45px; top: 231px; font-size: 38px; font-weight: 700; color: var(--navy); }
  .credentials {
    left: 45px; top: 275px;
    font-family: "PT Sans Narrow", sans-serif;
    font-size: 25px; line-height: 35px; color: var(--cyan);
  }

  .divider { left: 45px; top: 345px; width: 915px; height: 2px; background: var(--navy); }

  .contact-block { top: 368px; font-size: 27px; line-height: 35px; font-style: normal; }
  .contact-block h3 { margin: 0; font-size: 28px; font-weight: 700; color: var(--navy); line-height: 36px; }
  .contact-block p { margin: 0; }
  .contact-block .label { font-weight: 700; color: var(--navy); }
  .clinic-westbrook { left: 49px; }
  .clinic-ashford { left: 352px; }
  .specialty-links { left: 648px; }
  .specialty-links h3 + p { margin-bottom: 5px; }
</style>
</head>
<body>
  <section class="card" aria-label="Business card">
    <svg class="brand-mark" viewBox="0 0 170 170" aria-hidden="true">
      <circle cx="85" cy="85" r="85" fill="var(--cyan)"/>
    </svg>
    <p class="brand-name">Meridale Nutrition</p>
    <p class="brand-web">www.meridalenutrition.com.au</p>

    <h1 class="doctor-name">Dr Elan Marsh</h1>
    <p class="credentials">MBBS (NSW) MBiomedE FRACS (Ortho)<br>FAOrthA Orthopaedic Surgeon</p>

    <div class="divider"></div>

    <address class="contact-block clinic-westbrook">
      <h3>Westbrook</h3>
      <p>12-14 Harlow Road</p>
      <p>Westbrook NSW 2199</p>
      <p><span class="label">Tel:</span> 02 9000 4127</p>
      <p><span class="label">Fax:</span> 02 9000 4128</p>
    </address>

    <address class="contact-block clinic-ashford">
      <h3>Ashford</h3>
      <p>88 Linley Street</p>
      <p>Ashford NSW 2041</p>
      <p><span class="label">Tel:</span> 02 9000 8350</p>
      <p><span class="label">Fax:</span> 02 9000 8351</p>
    </address>

    <div class="contact-block specialty-links">
      <h3>Shoulder and Elbow</h3>
      <p>www.elanmarsh.com.au</p>
      <h3>Knee surgery</h3>
      <p>www.kneecarehub.com.au</p>
    </div>
  </section>
</body>
</html>
```